Healthy Meal Delivery Website Needs to be updated, current, fresh and modern

Hi there,

The current website i have is super old and outdated.

I would like a beautiful modern site that has all the same content as the previous except with a a new, modern and trustworthy feel.

The current website is https://tovalplatefresh.com/

Target Market(s)

Health Conscious Young Professionals

Industry/Entity Type

Food Service

Font styles to use
Sans Serif

Requirements
Must have
• Modern Trustworthy feel
Should not have
• Anything out dated or cheesy or scammy

```html
<!DOCTYPE html>
<html lang="en">
<head>
<meta charset="utf-8">
<title>Toval Plate Fresh</title>
<link href="https://fonts.googleapis.com/css2?family=Montserrat:wght@400;600;700;800&family=Open+Sans:ital,wght@0,400;0,600;1,400&display=swap" rel="stylesheet">
<style>
:root{
  --blue:#1ba4dc;
  --lime:#cfd61f;
  --dark:#3b3b3b;
  --darker:#2e2e2e;
  --ink:#333;
  --white:#fff;
  --muted:#666;
}
*{box-sizing:border-box;margin:0;padding:0}
html,body{width:1200px;height:3822px;overflow:hidden;background:var(--white)}
body{position:relative;font-family:'Open Sans',sans-serif;color:var(--ink)}
.abs{position:absolute}
h1,h2,h3,.nav a,.brand{font-family:'Montserrat',sans-serif}

/* header */
.brand{left:97px;top:26px;display:flex;align-items:center;gap:12px;font-weight:700;font-size:24px;color:var(--blue)}
.brand-dot{width:34px;height:34px;border-radius:50%;background:var(--lime)}
.contact-item{top:24px;font-family:'Montserrat',sans-serif;font-size:19px;white-space:nowrap}
.contact-item b{display:flex;align-items:center;gap:10px;font-weight:600;color:var(--ink)}
.contact-item span{display:block;margin-top:4px;color:var(--blue);font-size:15px}
.contact-item.phone span{color:var(--lime)}
.nav{left:97px;top:97px;width:1003px;height:56px;background:var(--blue);display:flex;align-items:center;justify-content:space-between;padding-right:14px}
.nav a{color:var(--white);text-decoration:none;font-size:15px;font-weight:600;line-height:56px;white-space:nowrap}
.nav a.active{background:var(--lime);padding:0 34px}

/* hero */
.hero{left:0;top:153px;width:1200px;height:472px;background:radial-gradient(ellipse at 40% 70%,#b07a3a 0%,#6a5240 35%,#3f3a36 70%,#2c2a28 100%)}
.hero-title{left:0;top:238px;width:1200px;text-align:center;color:var(--white);font-size:50px;font-weight:800;letter-spacing:1px}
.hero-tag{left:0;top:326px;width:1200px;text-align:center;color:var(--white);font-size:27px;font-weight:600;font-family:'Montserrat',sans-serif}
.arrow{width:30px;height:50px}

/* intro */
.intro-title{left:150px;top:842px;width:900px;text-align:center;color:var(--blue);font-size:27px;font-weight:700;line-height:40px}
.intro-text{left:99px;top:950px;width:1002px;text-align:center;font-size:15.5px;line-height:27px;color:var(--ink)}
.feature{top:1116px;width:251px;height:304px;text-align:center;color:var(--white);padding:106px 22px 0}
.feature.blue{background:var(--blue)}
.feature.lime{background:var(--lime)}
.feature h3{font-size:22px;font-weight:700;letter-spacing:.5px;margin-bottom:14px}
.feature p{font-size:13px;line-height:20px;height:104px}
.feature .btn{display:inline-block;border:2px solid var(--white);border-radius:20px;padding:6px 20px;font-size:13px;font-weight:600;margin-top:8px}
.feature-icon{top:1059px;width:124px;height:124px;border-radius:50%;border:6px solid var(--white);display:flex;align-items:center;justify-content:center}
.feature-icon.blue{background:var(--blue)}
.feature-icon.lime{background:var(--lime)}

/* plan */
.plan{left:0;top:1478px;width:1200px;height:726px;background:radial-gradient(ellipse at 50% 50%,#4a4a48 0%,#333 70%,#262626 100%)}
.section-title{left:0;width:1200px;text-align:center;font-size:30px;font-weight:700}
.rule{width:80px;height:2px;left:560px}
.step{width:228px;height:228px;border-radius:50%;border:6px solid var(--white);color:var(--white);text-align:center;display:flex;flex-direction:column;align-items:center;justify-content:center;padding:0 26px}
.step h3{font-size:15px;font-weight:700;margin:8px 0 8px;white-space:nowrap}
.step p{font-size:11px;line-height:16px}
.step.grey{background:#9a9a9a}
.step.lime{background:var(--lime)}
.step.blue{background:var(--blue);width:252px;height:252px}
.step.blue h3{font-size:19px}

/* menu */
.menu-text{left:99px;top:2270px;width:1002px;text-align:center;font-size:15.5px;line-height:27px}
.dish{top:2370px;width:321px;height:216px;border-radius:18px}
.dish-label{top:2608px;width:321px;text-align:center}
.dish-label h3{color:var(--blue);font-size:22px;font-weight:700}
.dish-label p{font-size:13px;margin-top:10px;color:var(--ink)}

/* testimonial */
.testimonial{left:0;top:2714px;width:1200px;height:726px;background:radial-gradient(ellipse at 50% 40%,#2d9fd6 0%,#1a83c0 55%,#1270ad 100%)}
.avatar{left:544px;top:2971px;width:112px;height:112px;border-radius:50%;background:#d9c3a8;border:5px solid var(--white)}
.quote{left:150px;top:3124px;width:900px;text-align:center;color:var(--white);font-style:italic;font-size:16px;line-height:31px}
.quote-name{left:0;top:3240px;width:1200px;text-align:center;color:var(--white);font-weight:700;font-size:20px;font-family:'Montserrat',sans-serif}

/* footer */
.footer{left:0;top:3440px;width:1200px;height:382px;background:var(--dark)}
.footer-title{color:var(--white);font-size:22px;font-weight:700;font-family:'Montserrat',sans-serif}
.footer-line{height:2px;background:linear-gradient(90deg,rgba(255,255,255,.8),rgba(255,255,255,0))}
.f-item{display:flex;align-items:center;gap:12px;color:var(--white);font-size:17px;font-weight:600;white-space:nowrap}
.ring{width:34px;height:34px;border-radius:50%;border:2px solid var(--white);display:flex;align-items:center;justify-content:center;flex:none}
.links{display:grid;grid-template-columns:170px 150px;row-gap:10px;color:var(--white);font-size:13px}
.links span::before{content:"";display:inline-block;width:8px;height:8px;border-radius:50%;background:var(--white);margin-right:18px;vertical-align:middle}
.copyright{left:0;top:3768px;width:1200px;text-align:center;color:var(--white);font-size:13px}
</style>
</head>
<body>

<!-- header -->
<div class="abs brand"><span class="brand-dot"></span>Toval Plate Fresh</div>
<div class="abs contact-item" style="left:660px">
  <b><svg width="24" height="18" viewBox="0 0 24 18"><rect x="1" y="1" width="22" height="16" fill="none" stroke="#1ba4dc" stroke-width="2"/><path d="M1 1l11 9 11-9" fill="none" stroke="#1ba4dc" stroke-width="2"/></svg>Email</b>
  <span>sales@tovalplatefresh.com</span>
</div>
<div class="abs contact-item phone" style="left:918px">
  <b><svg width="14" height="22" viewBox="0 0 14 22"><rect x="1" y="1" width="12" height="20" rx="2" fill="none" stroke="#cfd61f" stroke-width="2"/><circle cx="7" cy="17" r="1.5" fill="#cfd61f"/></svg>Phone</b>
  <span>416-555-0182</span>
</div>
<nav class="abs nav">
  <a class="active">HOME</a><a>TOVAL MEAL PLANS</a><a>MENU</a><a>PRICING</a><a>ABOUT</a><a>PRESS</a><a>CONTACT</a><a>SIGN UP</a><a>LOGIN</a>
</nav>

<!-- hero -->
<div class="abs hero" role="img" aria-label="Photo of a woman at a kitchen table behind a basket of fresh fruit"></div>
<svg class="abs" style="left:0;top:540px" width="1200" height="90" viewBox="0 0 1200 90" preserveAspectRatio="none"><path d="M0 0Q600 150 1200 0V90H0Z" fill="#fff"/></svg>
<h1 class="abs hero-title">TOVAL PLATE FRESH</h1>
<div class="abs hero-tag">"Fresh and so Delicious"</div>
<svg class="abs arrow" style="left:26px;top:337px" viewBox="0 0 30 50"><path d="M24 4L6 25l18 21" fill="none" stroke="#fff" stroke-width="3"/></svg>
<svg class="abs arrow" style="left:1144px;top:337px" viewBox="0 0 30 50"><path d="M6 4l18 21-18 21" fill="none" stroke="#fff" stroke-width="3"/></svg>

<!-- intro -->
<h2 class="abs intro-title">The Toval Plan Delivers Diet Meals To Your Door In Toronto, gta And Montreal</h2>
<p class="abs intro-text">Our fresh and delicious diet meals and snacks are made with only the best natural ingredients that nourish your body.  Why not let us prepare your meals while you lose the weight?</p>

<div class="abs feature blue" style="left:99px"><h3>HEALTHY</h3><p>The Toval Plan is a great way to ensure you are eating all the nutrients you need, and nothing your body doesn't need.</p><span class="btn">Read More</span></div>
<div class="abs feature lime" style="left:350px"><h3>CHOICE</h3><p>You can choose your own meals from over 100 tasty entrees, desserts and snack foods. You can choose your meals online.</p><span class="btn">Read More</span></div>
<div class="abs feature blue" style="left:600px"><h3>FRESH</h3><p>All of our meals are real food, freshly prepared by our in-house expert chefs.</p><span class="btn">Read More</span></div>
<div class="abs feature lime" style="left:850px"><h3>CUSTOMIZED</h3><p>Your meals will be delivered fresh to your door, customized for your unique body type and level of activity.</p><span class="btn">Read More</span></div>

<div class="abs feature-icon lime" style="left:163px"><svg width="56" height="56" viewBox="0 0 56 56"><path d="M28 44C14 34 10 27 10 20a9 9 0 0118-2 9 9 0 0118 2c0 7-4 14-18 24z" fill="none" stroke="#fff" stroke-width="3"/><path d="M8 48h40" stroke="#fff" stroke-width="3"/></svg></div>
<div class="abs feature-icon blue" style="left:413px"><svg width="56" height="56" viewBox="0 0 56 56"><g fill="none" stroke="#fff" stroke-width="3"><rect x="8" y="8" width="16" height="16" rx="3"/><rect x="32" y="8" width="16" height="16" rx="3"/><rect x="8" y="32" width="16" height="16" rx="3"/><rect x="32" y="32" width="16" height="16" rx="3"/><path d="M12 16l3 3 6-6M36 40l3 3 6-6"/></g></svg></div>
<div class="abs feature-icon lime" style="left:663px"><svg width="56" height="56" viewBox="0 0 56 56"><path d="M10 46C10 22 26 10 48 10c0 22-12 36-36 36z" fill="#fff"/><path d="M12 44L34 22" stroke="#cfd61f" stroke-width="3"/></svg></div>
<div class="abs feature-icon blue" style="left:913px"><svg width="56" height="56" viewBox="0 0 56 56"><g fill="none" stroke="#fff" stroke-width="3"><circle cx="22" cy="22" r="11" stroke-dasharray="5 3"/><circle cx="22" cy="22" r="4"/><circle cx="38" cy="38" r="9" stroke-dasharray="4 3"/><circle cx="38" cy="38" r="3"/></g></svg></div>

<!-- plan -->
<div class="abs plan" role="img" aria-label="Darkened photo of fresh salad ingredients"></div>
<svg class="abs" style="left:0;top:1470px" width="1200" height="100" viewBox="0 0 1200 100" preserveAspectRatio="none"><path d="M0 0H1200V20Q600 140 0 20Z" fill="#fff"/></svg>
<svg class="abs" style="left:0;top:2110px" width="1200" height="100" viewBox="0 0 1200 100" preserveAspectRatio="none"><path d="M0 100H1200V0Q600 140 0 80Z" fill="#fff"/></svg>
<h2 class="abs section-title" style="top:1636px;color:#fff">The Toval Plan</h2>
<div class="abs rule" style="top:1692px;background:#fff"></div>

<div class="abs step grey" style="left:72px;top:1776px">
  <svg width="40" height="36" viewBox="0 0 40 36"><g fill="none" stroke="#fff" stroke-width="2.5"><rect x="14" y="2" width="12" height="9"/><rect x="2" y="25" width="10" height="9"/><rect x="15" y="25" width="10" height="9"/><rect x="28" y="25" width="10" height="9"/><path d="M20 11v7M7 25v-7h26v7M20 18v7"/></g></svg>
  <h3>WHAT IS PHASE 2?</h3><p>Phase 2 reintroduces certain healthy carbs into your diet: whole grains.</p>
</div>
<div class="abs step lime" style="left:273px;top:1776px">
  <svg width="40" height="32" viewBox="0 0 40 32"><g fill="none" stroke="#fff" stroke-width="2.5"><rect x="2" y="2" width="36" height="10" rx="2"/><rect x="2" y="20" width="36" height="10" rx="2"/><path d="M8 7h10M8 25h18"/></g></svg>
  <h3>WHAT IS PHASE 1?</h3><p>Phase 1 is the stricter phase that eliminates bad carbs and processed foods.</p>
</div>
<div class="abs step lime" style="left:701px;top:1776px">
  <svg width="36" height="38" viewBox="0 0 36 38"><g fill="none" stroke="#fff" stroke-width="2.5"><rect x="5" y="6" width="26" height="30" rx="3"/><rect x="12" y="2" width="12" height="7"/><path d="M11 22l5 5 9-10"/></g></svg>
  <h3>SELECTION</h3><p>Choose your meals from over 100 delicious entrees, snacks and desserts.</p>
</div>
<div class="abs step grey" style="left:900px;top:1776px">
  <svg width="40" height="34" viewBox="0 0 40 34"><g fill="none" stroke="#fff" stroke-width="2.5"><path d="M10 2h20l8 10-18 20L2 12z"/><path d="M2 12h36M15 2l-3 10 8 20 8-20-3-10"/></g></svg>
  <h3>LUXURY</h3><p>Enjoy the luxury of having your own personal chef and nutritionist prepare your meals.</p>
</div>
<div class="abs step blue" style="left:475px;top:1764px">
  <svg width="48" height="48" viewBox="0 0 48 48"><circle cx="24" cy="24" r="21" fill="none" stroke="#fff" stroke-width="3"/><path d="M17 18a7 7 0 1110 6c-2 1-3 2-3 5" fill="none" stroke="#fff" stroke-width="3"/><circle cx="24" cy="35" r="2" fill="#fff"/></svg>
  <h3>WHAT YOU GET</h3><p>The Toval Plan provides you with 3 fresh daily meals and 3 snacks delivered.</p>
</div>

<!-- menu -->
<h2 class="abs section-title" style="top:2214px;color:var(--blue)">Select From Over 100 Menu Items</h2>
<p class="abs menu-text">You can choose your own meals from over 100 tasty entrees, desserts and snack foods. You can choose your meals online, or we can select your meals for you.</p>

<div class="abs dish" style="left:99px;background:linear-gradient(135deg,#e9e5df,#c8894a 60%,#a8682e)" role="img" aria-label="Photo of buttermilk cinnamon waffles"></div>
<div class="abs dish" style="left:441px;background:linear-gradient(135deg,#d9b98a,#c98d4d 50%,#6a8a3a)" role="img" aria-label="Photo of grilled chicken salad"></div>
<div class="abs dish" style="left:780px;background:linear-gradient(135deg,#5a3a28,#7a4a2e 50%,#4e6a2a)" role="img" aria-label="Photo of flat iron steak with roasted vegetables"></div>

<div class="abs dish-label" style="left:99px"><h3>BREAKFAST</h3><p>BUTTERMILK CINNAMON WAFFLES</p></div>
<div class="abs dish-label" style="left:441px"><h3>LUNCH</h3><p>GRILLED CHICKEN SALAD</p></div>
<div class="abs dish-label" style="left:780px"><h3>BREAKFAST</h3><p>FLAT IRON STEAK WITH ROASTED VEGETABLES</p></div>

<svg class="abs arrow" style="left:30px;top:2455px" viewBox="0 0 30 50"><path d="M24 4L6 25l18 21" fill="none" stroke="#1ba4dc" stroke-width="3"/></svg>
<svg class="abs arrow" style="left:1140px;top:2455px" viewBox="0 0 30 50"><path d="M6 4l18 21-18 21" fill="none" stroke="#1ba4dc" stroke-width="3"/></svg>

<!-- testimonial -->
<div class="abs testimonial" role="img" aria-label="Blue toned photo of fresh vegetables"></div>
<svg class="abs" style="left:0;top:2705px" width="1200" height="100" viewBox="0 0 1200 100" preserveAspectRatio="none"><path d="M0 0H1200V30Q600 120 0 10Z" fill="#fff"/></svg>
<svg class="abs" style="left:0;top:3350px" width="1200" height="92" viewBox="0 0 1200 92" preserveAspectRatio="none"><path d="M0 92V30Q600 -20 1200 50V92Z" fill="#3b3b3b"/></svg>
<h2 class="abs section-title" style="top:2866px;color:#fff">What They Say</h2>
<div class="abs rule" style="top:2922px;background:#fff"></div>
<div class="abs avatar" role="img" aria-label="Customer portrait photo"></div>
<p class="abs quote">Ok, so you know I loved Toval food the first time but somehow, the second time I love it even more. My lentil soup was incredible! And I am loooving these huge snacks - melba, cheese, veggies, turkey pepperoni - I feel like I am able to graze all day long! So brilliant!</p>
<div class="abs quote-name">- Dana</div>
<svg class="abs arrow" style="left:30px;top:3136px" viewBox="0 0 30 50"><path d="M24 4L6 25l18 21" fill="none" stroke="#fff" stroke-width="3"/></svg>
<svg class="abs arrow" style="left:1140px;top:3136px" viewBox="0 0 30 50"><path d="M6 4l18 21-18 21" fill="none" stroke="#fff" stroke-width="3"/></svg>

<!-- footer -->
<footer class="abs footer"></footer>
<h3 class="abs footer-title" style="left:106px;top:3486px">Contact Us</h3>
<div class="abs footer-line" style="left:106px;top:3530px;width:160px"></div>
<div class="abs f-item" style="left:102px;top:3572px"><span class="ring"><svg width="16" height="16" viewBox="0 0 16 16"><path d="M3 1l3 3-2 2c1 2 3 4 5 5l2-2 3 3-2 3C7 15 1 9 1 3z" fill="#fff"/></svg></span>416-555-0182</div>
<div class="abs f-item" style="left:102px;top:3620px;font-size:15px"><span class="ring"><svg width="16" height="12" viewBox="0 0 16 12"><rect x="1" y="1" width="14" height="10" fill="none" stroke="#fff" stroke-width="1.6"/><path d="M1 1l7 6 7-6" fill="none" stroke="#fff" stroke-width="1.6"/></svg></span>sales@tovalplatefresh.com</div>

<h3 class="abs footer-title" style="left:484px;top:3486px">Quick Contact</h3>
<div class="abs footer-line" style="left:484px;top:3530px;width:170px"></div>
<div class="abs links" style="left:486px;top:3578px">
  <span>Home</span><span>About</span>
  <span>Toval Meal Plans</span><span>Press</span>
  <span>Menu</span><span>Contact</span>
  <span>Pricing</span>
</div>

<h3 class="abs footer-title" style="left:936px;top:3486px">Social Media</h3>
<div class="abs footer-line" style="left:936px;top:3530px;width:160px"></div>
<div class="abs f-item" style="left:934px;top:3572px"><span class="ring"></span>Friendline</div>
<div class="abs f-item" style="left:934px;top:3628px"><span class="ring"></span>Snapgrid</div>

<div class="abs" style="left:106px;top:3735px;width:990px;height:1px;background:rgba(255,255,255,.45)"></div>
<p class="abs copyright">Copyrights © 2018 Toval Plate Fresh. All Rights Reserved</p>

</body>
</html>
```